Bold, Modern, Clean "Kestrelwaymassage.com" website

Why we stand out?
We are a male and female mobile massage team. Our names are Paul and Lina. 
Kestrel Way is a Seattle based mobile massage service. Our massage is offered to the community with a goal of facilitating balance within each individual. We specialize in integrated Pain management, and sports/medical massage therapy. Every client's first assessment is attended by our male and female massage therapist team. Depending on the goals identified for an individual determines which therapist will be assigned to provide treatment, if not both.

Our passion...
Here at Kestrel Way, we have a great passion for Postural Resoration and how it is integrated into an individual's Massage treatment. We pride ourselves in being natural facilitators of healing, which takes the ego of the therapist out of the client's healing process. We strive to deliver the best massage possible by including modalities such as Neuromuscular, Myofascial release, spontaneous muscle release, postural restoration, orthopedic, and medical massage.

Our education...

We are both Graduates of Venmora, school of massage therapy. We have continuing education in medical massage, myofacial release, trigger point therapy, postural restoration, anatomy, and spontaneous muscle release. Lina is also a Certified Yoga Instructor, which amplifies her experience with flexibility and strength as it pertains to each individual. Paul's passion is Massage, stretching, and strength training to encourage postural restoration and realignment.

Our rates-

Our rates are $75/ 60 minutes, $95/ 90 minutes, and $120/ 120 minutes.

Education-
Both Lina and I worked as behavioral health professionals that specialized in life skills mentoring for youth who had experienced different types of trauma. This led us both to want to help others in a different environment, where individuals can be empowered to take responsibility over their own healing. To us, massage is a type of manipulation physical therapy, that encourages healing on many levels.

Advice to any massage client-
The most important thing to 'us', as Licenced providers is to get you on to our table to show you our skills. But a good therapist never forgets that it's not about what we do for you, but what we can facilitate for you. Your health and healing has nothing to do with us. It is yours, not ours. Identify what your goals are with any Therapist, and know what the end looks like. Progress should be tangible, such as range of motion, and decreased pain.

Lina and Paul at Kestrel Way are awesome! I recently had open heart surgery, and Lina worked on me to increase my range of motion while helping with the pinched nerve from my arm being in the same position for so long during my surgery. My wife drives a lot for work, and Paul has helped decrease her neck and lower back pain immensely. They are seriously the best therapists I have ever worked with. I would recommend them to anyone who needs anything from stress relief to a medical massage treatment. They are professional, up beat, easy going, and always on time. And, I love that they meet us where ever we like! We did a staycation recently, where they came to our hotel to give us relaxation massages. Although usually they come to our home, where we focus on pain related issues. We will continue to work with them for a long, long time.

Target Market(s)

Mobile massage therapy clients

Industry/Entity Type

Massage Therapy

Coding

Coded - Design and coding required

Number of Pages Required

1 page

Font styles to use
Serif
Sans Serif

Requirements
Must have
• Please add or remove any information that would help the presentation of our website. Our logo is posted below, please include into the website.
• Please include a contact field that includes, kestrelwaymassage@fernmail.net,
• (206) 555-0148
• We have also included our own stock photos, as well as a photo of Paul and Lina. Please include a cropped photo of both massage therapists.

```html
<!DOCTYPE html>
<html lang="en">
<head>
<meta charset="utf-8">
<title>Kestrel Way – Mobile Massage</title>
<link rel="stylesheet" href="https://fonts.googleapis.com/css2?family=Open+Sans:wght@300;400;600;700&display=swap">
<style>
  :root{
    --teal:#1bc2ae;
    --teal-bright:#22d1bc;
    --teal-dark:#0e6f69;
    --teal-deep:#0a4d4a;
    --teal-mid:#108079;
    --navy:#0f2a6b;
    --ink:#444;
    --muted:#777;
    --light:#efefef;
    --white:#fff;
  }
  *{box-sizing:border-box;margin:0;padding:0}
  html,body{width:1200px;height:2640px;overflow:hidden}
  body{font-family:"Open Sans",Arial,sans-serif;color:var(--ink);background:var(--white);position:relative}

  /* hero */
  .hero{position:absolute;left:0;top:0;width:1200px;height:680px;
    background:linear-gradient(90deg,#2a2420 0%,#4a3a30 28%,#c9a58c 50%,#f1dccb 68%,#f7ece3 100%)}
  .hero-shade{position:absolute;left:0;top:0;width:520px;height:680px;background:linear-gradient(90deg,rgba(0,0,0,.45),rgba(0,0,0,0))}
  .logo{position:absolute;left:84px;top:22px;width:150px;height:150px;border-radius:50%;background:var(--navy);
    display:flex;align-items:center;justify-content:center;text-align:center;color:var(--white);
    font-weight:700;font-size:22px;line-height:1.15}
  .main-nav{position:absolute;left:0;top:220px;width:470px}
  .nav-item{position:relative;height:56px;margin-bottom:28px;background:rgba(0,0,0,.42);display:flex;align-items:center;
    padding-left:74px;color:var(--white);font-size:15px;letter-spacing:.5px;text-transform:uppercase}
  .nav-item .rule{position:absolute;left:230px;right:70px;top:50%;height:1px;background:rgba(255,255,255,.7)}
  .nav-item .dot{position:absolute;right:62px;top:50%;width:12px;height:12px;margin-top:-6px;border:2px solid #fff;border-radius:50%;background:rgba(0,0,0,.3)}
  .nav-item svg{position:absolute;right:14px;top:50%;margin-top:-12px}

  /* services */
  .services{position:absolute;left:0;top:680px;width:1200px;height:300px;display:flex}
  .service{width:300px;color:var(--white);text-align:center}
  .service-tab{height:60px;display:flex;align-items:center;justify-content:center;font-size:15px;font-weight:600;background:var(--teal-deep)}
  .service-body{height:240px;padding:26px 40px 0}
  .service:nth-child(1) .service-body{background:var(--teal-bright)}
  .service:nth-child(2) .service-body{background:var(--teal-mid)}
  .service:nth-child(3) .service-body{background:#0d746e}
  .service:nth-child(4) .service-body{background:#0b625d}
  .service:nth-child(1) .service-tab{background:#0a3f3d}
  .service-icon{width:54px;height:54px;margin:0 auto 18px;border-radius:8px;background:rgba(255,255,255,.35)}
  .service p{font-size:13px;line-height:1.55;opacity:.95}

  /* section heads */
  .section-title{text-align:center;font-weight:300;font-size:44px;color:#555}
  .divider{display:flex;align-items:center;justify-content:center;gap:16px;margin:14px 0 0}
  .divider span{display:block;width:180px;height:1px;background:#bbb}

  .education{position:absolute;left:0;top:980px;width:1200px;height:400px;padding-top:46px}
  .education p,.about p{width:940px;margin:40px auto 0;text-align:center;font-size:14px;line-height:1.75;color:var(--muted)}
  .actions{display:flex;justify-content:center;gap:22px;margin-top:48px}
  .btn{width:170px;height:46px;display:flex;align-items:center;justify-content:center;font-size:13px;font-weight:600;text-transform:uppercase;color:var(--white);background:var(--teal);border:2px solid var(--teal)}
  .btn.outline{background:transparent;color:var(--teal-dark)}

  /* testimonial */
  .testimonial{position:absolute;left:0;top:1380px;width:1200px;height:400px;
    background:linear-gradient(90deg,#6a5040 0%,#3e2c22 30%,#2f2219 60%,#5c4434 100%);color:var(--white);text-align:center;padding-top:38px}
  .testimonial .section-title{color:var(--white)}
  .testimonial .divider span{background:rgba(255,255,255,.7)}
  .testimonial blockquote{width:980px;margin:26px auto 0;font-size:14px;line-height:1.7}
  .testimonial cite{display:block;margin-top:20px;font-style:normal;font-size:16px}
  .dots{display:flex;justify-content:center;gap:10px;margin-top:40px}
  .dots i{width:10px;height:10px;border-radius:50%;background:rgba(255,255,255,.6)}
  .dots i.on{background:var(--white)}

  .about{position:absolute;left:0;top:1780px;width:1200px;height:440px;padding-top:50px}
  .about .actions{margin-top:40px}

  /* contact */
  .contact{position:absolute;left:0;top:2220px;width:1200px;height:120px;background:var(--light);display:flex;align-items:center;justify-content:center;gap:220px}
  .contact-item{display:flex;align-items:center;gap:22px;font-size:16px;color:#555}
  .contact-icon{width:56px;height:56px;background:var(--teal);display:flex;align-items:center;justify-content:center}

  /* footer */
  .footer{position:absolute;left:0;top:2340px;width:1200px;height:300px;
    background:linear-gradient(90deg,#cfe3ee 0%,#9fc6da 22%,#eef3f5 48%,#e7d6c8 75%,#d9bfa9 100%)}
  .footer-logo{position:absolute;left:540px;top:18px;width:120px;height:120px;border-radius:50%;background:var(--navy);
    display:flex;align-items:center;justify-content:center;text-align:center;color:var(--white);font-weight:700;font-size:18px;line-height:1.15}
  .social{position:absolute;left:0;width:1200px;top:168px;display:flex;justify-content:center;gap:14px}
  .social i{width:46px;height:46px;background:var(--teal-mid)}
  .copyright{position:absolute;left:0;width:1200px;top:236px;text-align:center;font-size:13px;color:#335}
</style>
</head>
<body>

<header class="hero" role="img" aria-label="Photo of a client receiving a relaxing head massage">
  <div class="hero-shade"></div>
</header>
<div class="logo">Kestrel<br>Way</div>

<nav class="main-nav">
  <div class="nav-item">Home<span class="rule"></span><span class="dot"></span>
    <svg width="24" height="24" viewBox="0 0 24 24" fill="#fff"><path d="M12 3 2 12h3v9h5v-6h4v6h5v-9h3z"/></svg></div>
  <div class="nav-item">About Us<span class="rule"></span><span class="dot"></span>
    <svg width="24" height="24" viewBox="0 0 24 24" fill="#fff"><circle cx="12" cy="7" r="4.5"/><path d="M3 22c0-5 4-8 9-8s9 3 9 8z"/></svg></div>
  <div class="nav-item">Education<span class="rule"></span><span class="dot"></span>
    <svg width="24" height="24" viewBox="0 0 24 24" fill="#fff"><path d="M12 4 1 9l11 5 11-5z"/><path d="M5 12v5c2 2 12 2 14 0v-5l-7 3z"/></svg></div>
  <div class="nav-item">Testimonial<span class="rule"></span><span class="dot"></span>
    <svg width="24" height="24" viewBox="0 0 24 24" fill="#fff"><path d="M3 4h18v12H9l-5 4v-4H3z"/></svg></div>
  <div class="nav-item">Contact Us<span class="rule"></span><span class="dot"></span>
    <svg width="24" height="24" viewBox="0 0 24 24" fill="#fff"><rect x="7" y="2" width="10" height="20" rx="2"/><rect x="9" y="5" width="6" height="11" fill="#333"/></svg></div>
</nav>

<section class="services">
  <div class="service"><div class="service-tab">Neuromuscular</div>
    <div class="service-body"><div class="service-icon" role="img" aria-label="Neuromuscular therapy icon"></div>
      <p>Targeted pressure on trigger points to calm nerves and ease chronic muscle pain.</p></div></div>
  <div class="service"><div class="service-tab">Spontaneous Muscle Release</div>
    <div class="service-body"><div class="service-icon" role="img" aria-label="Muscle release icon"></div>
      <p>Gentle positioning lets tight muscles release on their own without force or strain.</p></div></div>
  <div class="service"><div class="service-tab">postural restoration</div>
    <div class="service-body"><div class="service-icon" role="img" aria-label="Posture icon"></div>
      <p>Balanced work on posture patterns to realign the body and free easy movement.</p></div></div>
  <div class="service"><div class="service-tab">Medical Massage</div>
    <div class="service-body"><div class="service-icon" role="img" aria-label="Medical massage icon"></div>
      <p>Clinical massage planned around injury, surgery or pain goals for lasting relief.</p></div></div>
</section>

<section class="education">
  <h2 class="section-title">See Our Education</h2>
  <div class="divider"><span></span>
    <svg width="34" height="26" viewBox="0 0 24 18" fill="#888"><path d="M12 1 1 6l11 5 11-5z"/><path d="M5 9v4c2 2 12 2 14 0V9l-7 3z"/></svg><span></span></div>
  <p>We are both Graduates of Venmora, school of massage therapy. We have continuing education in medical massage, myofacial release, trigger point therapy, postural restoration, anatomy, and spontaneous muscle release. Lina is also a Certified Yoga Instructor, which amplifies her experience with flexibility and strength as it pertains to each individual.</p>
  <div class="actions"><span class="btn">Read More</span><span class="btn outline">Our Rate</span></div>
</section>

<section class="testimonial" role="img" aria-label="Spa photo with candles and flowers behind the testimonial">
  <h2 class="section-title">What Our Clients Say</h2>
  <div class="divider"><span></span>
    <svg width="30" height="26" viewBox="0 0 24 20" fill="#fff"><path d="M2 2h20v12H9l-5 4v-4H2z"/></svg><span></span></div>
  <blockquote>Lina and Paul at Kestrel Way are awesome! I recently had open heart surgery, and Lina worked on me to increase my range of motion while helping with the pinched nerve from my arm being in the same position for so long during my surgery. My wife drives a lot for work, and Paul has helped decrease her neck and lower back pain immensely. They are seriously the best therapists I have ever worked with.
    <cite>- Darcy T.</cite></blockquote>
  <div class="dots"><i class="on"></i><i></i><i></i><i></i><i></i></div>
</section>

<section class="about">
  <h2 class="section-title">Know About Us</h2>
  <div class="divider"><span></span>
    <svg width="26" height="26" viewBox="0 0 24 24" fill="#888"><circle cx="12" cy="7" r="4.5"/><path d="M3 22c0-5 4-8 9-8s9 3 9 8z"/></svg><span></span></div>
  <p>We are a male and female mobile massage team. Our names are Paul and Lina.<br>
  Kestrel Way is a Seattle based mobile massage service. Our massage is offered to the community with a goal of facilitating balance within each individual. We specialize in integrated Pain management, and sports/medical massage therapy. Every client's first assessment is attended by our male and female massage therapist team.</p>
  <div class="actions"><span class="btn">Read More</span></div>
</section>

<section class="contact">
  <div class="contact-item"><span class="contact-icon">
    <svg width="26" height="26" viewBox="0 0 24 24" fill="#fff"><path d="M6.6 10.8a15 15 0 0 0 6.6 6.6l2.2-2.2c.3-.3.7-.4 1-.2 1.1.4 2.3.6 3.6.6.6 0 1 .4 1 1V20c0 .6-.4 1-1 1A17 17 0 0 1 3 4c0-.6.4-1 1-1h3.5c.6 0 1 .4 1 1 0 1.3.2 2.5.6 3.6.1.3 0 .7-.2 1z"/></svg>
  </span>(206) 555-0148</div>
  <div class="contact-item"><span class="contact-icon">
    <svg width="28" height="22" viewBox="0 0 28 22"><rect x="1" y="1" width="26" height="20" fill="#fff"/><path d="M1 1l13 11L27 1" fill="none" stroke="#1bc2ae" stroke-width="2"/></svg>
  </span>kestrelwaymassage@fernmail.net</div>
</section>

<footer class="footer" role="img" aria-label="Photo of a relaxed client with a spa flower">
  <div class="footer-logo">Kestrel<br>Way</div>
  <div class="social"><i></i><i></i><i></i><i></i></div>
  <div class="copyright">© 2015 Kestrel Way. All rights reserved.</div>
</footer>

</body>
</html>
```